African homeware retailer needs a web page design

We need a web page design for a new homeware and accessories store based in Johannesburg, South Africa. Our store carries modern African inspired items from designers that support social development and poverty alleviation initiatives. We have a particular preference for outfits that are centred on the empowerment of women.

Our business celebrates the skill, design and product of African craft and the work of designers looking to take that forward in a socially beneficial way (creating employment, developing skills, supporting local crafts people etc). We aim to carry items and inspirations from all over the African continent.

We would like to see a design that communicates African beauty and elegance without the typical tribal references that are made in reference to African craft or art.

We would like the web page to be stylish, uncomplicated, modern, captivating and appealing to the discerning customer. A similar value proposition is that of http://www.marlowtenwick.example/.

This is an e-commerce website which must be attractive to both individual buyers and design professionals so the website needs to look professional.

Here are links to some websites we like:
http://www.quenbyhollis.example/
http://www.dravelo.example/

Our logo is attached to the brief.

Target Market(s)

Our target market is female, age 20-50. However should not alienate the design conscious male customer therefore

Industry/Entity Type

E-Commerce

Requirements
Must have
• - A featured product banner which includes a photograph and text. This should be easy to edit as we will be changing the featured product regularly
- An easily expendable products section with categories. Examples of categories could be cushions, bedding, crockery etc. Should be easy to add new categories as well as new product pictures
- Home/landing page should be uncluttered
- Should use the logo and should be easy to change the logo which we have in various colour combinations. We plan to change the logo colours depending on circumstance e.g. make it red and white around Valentines day (similar to the way Vintrel frequently changes the logo on their landing page)

```html
<!DOCTYPE html>
<html lang="en">
<head>
<meta charset="utf-8">
<title>Sahel &amp; Hearth – African Homeware</title>
<link href="https://fonts.googleapis.com/css2?family=Oxygen:wght@400;700&display=swap" rel="stylesheet">
<style>
:root{
  --navy:#0f4868;
  --cream:#fdf6da;
  --green:#3a9a46;
  --green-dark:#2f8a3b;
  --green-text:#2e9340;
  --hero-light:#d6edc8;
  --hero-mid:#7cc480;
  --hero-edge:#4fae5f;
  --grey-text:#555;
  --line:#d8d8d8;
  --card-bg:#eeeeee;
  --taupe:#9b8466;
  --white:#fff;
}
*{box-sizing:border-box;margin:0;padding:0}
html,body{width:1200px;height:2195px;overflow:hidden}
body{position:relative;background:var(--white);font-family:'Oxygen',sans-serif;color:var(--grey-text)}
.abs{position:absolute}
a{color:inherit;text-decoration:none}

.top-bar{left:0;top:0;width:1200px;height:22px;background:var(--navy);color:var(--white);font-size:12px;font-weight:700}
.top-bar ul{position:absolute;right:186px;top:3px;display:flex;list-style:none}
.top-bar li+li::before{content:"|";margin:0 9px;font-weight:400}

.site-header{left:0;top:22px;width:1200px;height:156px;background:var(--cream)}
.brand{left:186px;top:56px;display:flex;align-items:center;gap:10px;color:var(--green-text);font-size:26px;font-weight:700}
.brand-mark{width:22px;height:22px;background:var(--navy)}
.phone{right:187px;top:36px;display:flex;align-items:center;gap:8px;color:var(--green-text);font-size:23px;font-weight:700}
.search{right:186px;top:102px;width:222px;height:20px;border:1px solid #c9c9c9;background:var(--white);font-size:12px;padding:2px 6px;color:#333}
.search svg{position:absolute;right:4px;top:2px}

.main-nav{left:0;top:178px;width:1200px;height:33px;background:var(--navy)}
.main-nav ul{position:absolute;left:188px;top:0;display:flex;list-style:none;color:var(--white);font-size:13.5px;height:33px;align-items:center}
.main-nav li{padding:0 11px;line-height:33px}
.main-nav li.active{background:var(--green);font-weight:700;margin-right:5px}

.hero{left:0;top:211px;width:1200px;height:525px;background:radial-gradient(ellipse 520px 360px at 760px 300px,var(--hero-light),var(--hero-mid) 60%,var(--hero-edge));border-bottom:3px solid #9fc79a}
.hero-title{left:187px;top:300px;width:300px;color:var(--white);font-size:40px;font-weight:700;line-height:50px}
.hero-text{left:187px;top:418px;width:300px;color:var(--white);font-size:20px;line-height:26px}
.hero-photo{left:520px;top:222px;width:490px;height:488px;border-radius:40px;background:radial-gradient(ellipse at 50% 45%,#f0f0ec,#b9c9b0 55%,rgba(150,190,140,0) 75%)}
.btn-read{left:181px;top:640px;width:264px;height:43px;background:var(--green-dark);border-radius:4px;color:var(--white);font-size:25px;font-weight:700;display:flex;align-items:center;padding-left:34px;gap:18px;box-shadow:0 10px 14px -8px rgba(0,0,0,.25)}
.arrow-dot{display:inline-flex;width:28px;height:28px;border-radius:50%;background:var(--white);color:var(--green-dark);align-items:center;justify-content:center;font-size:13px}

.promo-card{top:758px;width:268px;height:347px}
.promo-card .photo{height:237px;background:var(--card-bg);border:1px solid var(--line)}
.promo-card .caption{height:73px;border:1px solid var(--line);border-top:none;text-align:center;padding-top:10px}
.promo-card h3{color:var(--green-text);font-size:19px;line-height:24px}
.promo-card p{font-size:19px;line-height:24px}
.promo-card .btn{margin-top:5px;height:32px;background:var(--green);color:var(--white);font-size:12.5px;display:flex;align-items:center;justify-content:center;gap:8px}
.promo-card .btn .arrow-dot{width:19px;height:19px;font-size:9px}

.soft-rule{left:210px;width:780px;height:14px;border-radius:50%;box-shadow:0 7px 8px -6px rgba(0,0,0,.18)}

.section-title{left:186px;width:828px;text-align:center;color:var(--green-text);font-size:29px;font-weight:700}
.rule{left:186px;width:828px;height:2px;background:var(--line)}
.chevron{color:#999;font-size:30px}

.product{top:1244px;width:195px;text-align:center}
.product .photo{height:193px}
.product h4{margin-top:19px;color:var(--navy);font-size:15px}
.product p{font-size:13px;line-height:18px;margin-top:2px}

.category{top:1670px;width:242px;height:33px;border:1px solid #d0d0d0;background:linear-gradient(#fbfbfb,#ececec);color:var(--green-text);font-size:19px;text-align:center;line-height:31px}

.subscribe-bar{left:186px;top:1797px;width:828px;height:53px;border-top:2px solid #e5e5e5;border-bottom:2px solid #e5e5e5}
.subscribe-bar .divider{position:absolute;left:423px;top:0;width:2px;height:49px;background:#e5e5e5}
.label-green{color:var(--green-text);font-size:20px;font-weight:700}
.email-field{left:326px;top:1810px;width:166px;height:25px;border:1px solid #ccc;background:#eee;font-size:12px;color:#aaa;padding:5px 8px}
.btn-submit{left:502px;top:1810px;width:78px;height:25px;background:var(--taupe);color:var(--white);font-size:15px;text-align:center;line-height:25px;border-radius:2px}
.pay-chip{top:1808px;height:32px;border:1px solid #ccc;background:var(--white);font-size:11px;font-weight:700;color:var(--navy);text-align:center;line-height:30px}

.site-footer{left:0;top:1904px;width:1200px;height:265px;background:var(--green);border-top:3px solid #2c7f38;color:var(--white)}
.footer-heading{font-size:18px}
.footer-links{list-style:none;font-size:12.5px;line-height:21.5px}
.field{left:380px;width:246px;height:24px;background:var(--white);border-radius:2px;font-size:10px;font-style:italic;color:#777;padding:5px 8px}
.btn-footer{left:380px;top:2132px;width:59px;height:21px;background:var(--navy);font-size:12px;font-weight:700;text-align:center;line-height:21px;border-radius:2px}
.social{list-style:none;font-size:11.5px;line-height:31.5px}
.social li{display:flex;align-items:center;gap:8px}
.social .sq{width:22px;height:22px;background:#c8a98a;display:inline-block}
.copyright{left:0;top:2169px;width:1200px;height:26px;background:var(--navy);border-top:3px solid #f6e98a;color:var(--white);font-size:11px;text-align:center;line-height:23px}
</style>
</head>
<body>

<div class="abs top-bar"><ul><li>Login</li><li>Sign Up</li><li>My Account</li><li>Shopping Cart</li></ul></div>

<header class="abs site-header"></header>
<div class="abs brand"><span class="brand-mark"></span>Sahel &amp; Hearth</div>
<div class="abs phone">
  <svg width="26" height="26" viewBox="0 0 26 26"><circle cx="13" cy="13" r="11.5" fill="none" stroke="#111" stroke-width="2"/><path d="M9 7c1-.8 2 .2 2.6 1.5.5 1-.3 1.5-.8 2 .7 1.6 1.8 2.8 3.4 3.6.6-.5 1.1-1.3 2.1-.7 1.2.7 2.2 1.6 1.4 2.6-1.2 1.5-3.2 1.4-5.4-.1C9.8 14 8 11.5 7.9 9.6 7.8 8.4 8.2 7.6 9 7z" fill="#111"/></svg>
  011-555-0142
</div>
<div class="abs search">Search
  <svg width="14" height="14" viewBox="0 0 14 14"><circle cx="5.5" cy="5.5" r="4.2" fill="none" stroke="#111" stroke-width="1.6"/><path d="M8.6 8.6l4 4" stroke="#111" stroke-width="1.8"/></svg>
</div>

<nav class="abs main-nav"><ul>
  <li class="active">Shop Now</li><li>Our Story</li><li>Blog</li><li>Custom Design</li><li>Our Shop</li><li>Press &amp; Mentions</li><li>Designer &amp; Architects</li><li>Video</li><li>Contact</li>
</ul></nav>

<section class="abs hero"></section>
<div class="abs hero-photo" role="img" aria-label="Featured product photo: beaded zebra figure with carved wooden bowl"></div>
<h1 class="abs hero-title">Lorem ipsum dolor sit</h1>
<p class="abs hero-text">Lorem ipsum dolor sit amet consectetuer adipiscing elit sed diam nonummy nibh euismod tincidunt ut laoreet dolore magna aliquam erat volutpat.</p>
<a class="abs btn-read">READ MORE <span class="arrow-dot">&gt;&gt;</span></a>

<article class="abs promo-card" style="left:186px">
  <div class="photo" role="img" aria-label="Craft magazines" style="background:linear-gradient(135deg,#eee,#c9b79c 40%,#8a8f93 60%,#eee)"></div>
  <div class="caption"><h3>Lorem ipsum dolor sit</h3><p>Lorem ipsum dolor sit</p></div>
  <a class="btn">BROWSE OUR CATALOG <span class="arrow-dot">&gt;&gt;</span></a>
</article>
<article class="abs promo-card" style="left:467px">
  <div class="photo" role="img" aria-label="Carved wooden serving bowls" style="background:radial-gradient(ellipse 110px 45px at 50% 55%,#b46f3c,#d79a63 70%,#eeeeee 72%)"></div>
  <div class="caption"><h3>Lorem ipsum dolor sit</h3><p>Lorem ipsum dolor sit</p></div>
  <a class="btn">SHOP NEW ITEMS <span class="arrow-dot">&gt;&gt;</span></a>
</article>
<article class="abs promo-card" style="left:746px">
  <div class="photo" role="img" aria-label="Pile of colourful striped cushions" style="background:radial-gradient(ellipse 120px 80px at 50% 55%,#2b3f8f,#c8342d 45%,#e7b23a 65%,#eeeeee 80%)"></div>
  <div class="caption"><h3>Lorem ipsum dolor sit</h3><p>Lorem ipsum dolor sit</p></div>
  <a class="btn">READ MORE <span class="arrow-dot">&gt;&gt;</span></a>
</article>

<div class="abs soft-rule" style="top:1120px"></div>

<h2 class="abs section-title" style="top:1180px">Featured Product</h2>
<span class="abs chevron" style="left:184px;top:1180px">&#8249;</span>
<span class="abs chevron" style="left:998px;top:1178px">&#8250;</span>
<div class="abs rule" style="top:1216px"></div>

<div class="abs product" style="left:187px"><div class="photo" role="img" aria-label="Colourful fabric belts and bags" style="background:linear-gradient(135deg,#2d6f8a,#c83a6b 45%,#d9a13a)"></div><h4>Product Name</h4><p>Lorem ipsum dolor sit amet<br>consectetuer adipiscing</p></div>
<div class="abs product" style="left:397px"><div class="photo" role="img" aria-label="Cushions on a window seat" style="background:linear-gradient(#e8e4da,#b98c8f 55%,#c9416e)"></div><h4>Product Name</h4><p>Lorem ipsum dolor sit amet<br>consectetuer adipiscing</p></div>
<div class="abs product" style="left:609px"><div class="photo" role="img" aria-label="Woven lidded baskets" style="background:radial-gradient(ellipse at 50% 55%,#d7b57a,#a47a3f 55%,#3a3630)"></div><h4>Product Name</h4><p>Lorem ipsum dolor sit amet<br>consectetuer adipiscing</p></div>
<div class="abs product" style="left:817px"><div class="photo" role="img" aria-label="Tan leather tote bag" style="background:radial-gradient(ellipse 60px 80px at 50% 58%,#b8864e,#d1a874 60%,#fafafa 80%);border:1px solid var(--line)"></div><h4>Product Name</h4><p>Lorem ipsum dolor sit amet<br>consectetuer adipiscing</p></div>

<div class="abs soft-rule" style="top:1528px"></div>

<h2 class="abs section-title" style="top:1582px">Categories</h2>
<div class="abs rule" style="top:1627px"></div>
<span class="abs chevron" style="left:184px;top:1664px">&#8249;</span>
<div class="abs category" style="left:218px">Cushions</div>
<div class="abs category" style="left:481px">Bedding</div>
<div class="abs category" style="left:740px">Crockery</div>
<span class="abs chevron" style="left:1000px;top:1664px">&#8250;</span>

<div class="abs soft-rule" style="top:1730px"></div>

<div class="abs subscribe-bar"><span class="divider"></span></div>
<span class="abs label-green" style="left:202px;top:1808px">Newsletter:</span>
<div class="abs email-field">Your Email Address:</div>
<div class="abs btn-submit">SUBMIT</div>
<span class="abs label-green" style="left:634px;top:1808px">We Accept:</span>
<div class="abs pay-chip" style="left:765px;width:56px">PayWell</div>
<div class="abs pay-chip" style="left:832px;width:47px">Varda</div>
<div class="abs pay-chip" style="left:890px;width:58px;line-height:14px;padding-top:2px">Varda<br>Spark</div>
<div class="abs pay-chip" style="left:955px;width:50px">Mondcard</div>

<footer class="abs site-footer"></footer>
<h3 class="abs footer-heading" style="left:206px;top:1924px;color:var(--white);font-weight:400">Quick Links</h3>
<ul class="abs footer-links" style="left:208px;top:1963px;color:var(--white)">
  <li>Shop Now</li><li>Our Story</li><li>Blog</li><li>Custom Design</li><li>Our Shop</li><li>Press &amp; Mentions</li><li>Designer &amp; Architects</li><li>Video</li><li>Contact</li>
</ul>
<h3 class="abs footer-heading" style="left:381px;top:1924px;color:var(--white);font-weight:400">QUICK CONTACT</h3>
<div class="abs field" style="top:1967px">Name</div>
<div class="abs field" style="top:1997px">Phone</div>
<div class="abs field" style="top:2027px">Email</div>
<div class="abs field" style="top:2057px;height:62px">Message</div>
<div class="abs btn-footer" style="color:var(--white)">Submit</div>
<h3 class="abs footer-heading" style="left:676px;top:1924px;color:var(--white);font-weight:400">Follow Us On</h3>
<ul class="abs social" style="left:676px;top:1962px;color:var(--white)">
  <li><span class="sq"></span>Facebond</li>
  <li><span class="sq"></span>Linkwell</li>
  <li><span class="sq"></span><u>Chirrup</u></li>
  <li><span class="sq"></span>Tackwall</li>
  <li><span class="sq"></span>Yodelo</li>
</ul>

<div class="abs copyright">© Copyright 2014. Sahel &amp; Hearth. All Rights Reserved.</div>

</body>
</html>
```